Website Design for a Project Management Consulting Business

I have a logo design already and now I need a website.
I am a project manager and run my own consulting business.
Currently I am under contract with 3 major Vantage 400 companies. I'd like a website I can direct current and future clients.
My job is running IT projects and working with developers to deliver business priorities.
The website should be professional and clean - I work IT projects and would like to incorporate that into any theme.
I'd like the site to have several page or breakoff links - sections would include : about me, about my services, a page to display all of my certification badges, another page to talk about highlights from past projects and so on.
Looking for a collaborative experience.

Industry/Entity Type

Vantage 400 Consulting Firm - Project Management

Coding

Coded - Design and coding required

Number of Pages Required

1 page

Font styles to use
Serif

Colors
0094D4
00A9DD
6FCCEA
C7EBF8
E9F6FB
EE7325
F08F49
F5BC92
FAE3D3
FDF4ED

Requirements
Must have
• Sections that are a must: About Me (bio), About My Services, About my Certifications and Credentials, Experience on Past Projects,
Nice to have
• I have added the logo below - I'd like to use the logo and have it prominent ; should be professional and inviting

```html
<!DOCTYPE html>
<html lang="en">
<head>
<meta charset="utf-8">
<title>Meridian – Project Management</title>
<link href="https://fonts.googleapis.com/css2?family=Audiowide&family=Roboto:wght@400;500;700&display=swap" rel="stylesheet">
<style>
:root{
  --blue:#0094D4;
  --blue-2:#00A9DD;
  --blue-3:#6FCCEA;
  --blue-pale:#C7EBF8;
  --blue-mist:#E9F6FB;
  --navy:#0a2a4a;
  --orange:#EE7325;
  --orange-2:#F08F49;
  --orange-3:#F5BC92;
  --ink:#1a1a1a;
  --text:#333;
  --black:#050505;
  --white:#fff;
}
*{box-sizing:border-box;margin:0;padding:0}
html,body{width:1200px;height:3637px;overflow:hidden}
body{position:relative;font-family:"Roboto",Arial,sans-serif;color:var(--text);background:linear-gradient(180deg,var(--white) 0,var(--blue-mist) 40%,var(--white) 100%)}
.abs{position:absolute}
.display{font-family:"Audiowide","Roboto",sans-serif;text-transform:uppercase}

/* header */
.topline{left:0;top:0;width:1200px;height:4px;background:var(--blue)}
.header{left:0;top:4px;width:1200px;height:81px;background:var(--white)}
.brand{display:flex;align-items:center;gap:10px}
.brand-square{width:34px;height:34px;border:3px solid currentColor}
.brand-name{font-family:"Roboto",sans-serif;font-weight:700;font-size:25px;letter-spacing:2px}
.header .brand{position:absolute;left:103px;top:22px;color:var(--navy)}
.nav{position:absolute;left:382px;top:32px;display:flex;gap:23px;font-size:15px;color:#222}
.nav a{color:inherit;text-decoration:none}
.nav .active{color:var(--blue);border-bottom:2px solid var(--blue);padding-bottom:4px}
.phone{position:absolute;left:798px;top:26px;display:flex;align-items:center;gap:12px;font-size:15px;color:#222}
.phone-icon{width:36px;height:36px;border-radius:50%;background:var(--blue);display:flex;align-items:center;justify-content:center}
.login{position:absolute;left:981px;top:25px;width:107px;height:41px;background:var(--blue);color:var(--white);font-weight:700;font-size:15px;display:flex;align-items:center;justify-content:center;gap:8px;border-radius:2px}

/* hero */
.hero-text{left:741px;top:312px;color:var(--white)}
.hero-kicker{font-size:19px;letter-spacing:1px;color:#e6f2fa}
.hero-title{font-size:58px;line-height:1;margin-top:12px;letter-spacing:1px}
.hero-lead{font-size:15px;line-height:28px;margin-top:22px;width:360px;color:#e2eef6}
.btn{display:inline-flex;align-items:center;gap:14px;font-weight:700;font-size:15px;text-transform:uppercase}
.hero-btn{position:absolute;left:2px;top:189px;width:170px;height:57px;padding-left:19px;background:var(--navy);color:var(--white);border-bottom:3px solid var(--blue);border-right:3px solid var(--blue)}
.slides{left:1128px;top:388px;font-weight:700;font-size:19px;line-height:39px;color:var(--white)}
.slides .on{color:var(--blue)}

/* section titles */
.section-title{left:0;width:1200px;text-align:center;font-size:35px;color:var(--ink);letter-spacing:1px}
.title-bar{left:561px;width:78px;height:4px;background:var(--blue)}

/* certifications */
.cert{width:300px;text-align:center;font-size:15px;color:#222}
.cert svg{display:block;margin:0 auto 18px}

/* services */
.card{width:231px;height:322px;background:var(--white);box-shadow:0 2px 8px rgba(0,0,0,.12)}
.card-photo{height:150px;background:linear-gradient(135deg,#5a3a2a 0,#c9a46e 45%,#e7e2d8 70%,#6d7d5a 100%)}
.card-body{padding:22px 16px 0}
.card-title{font-weight:700;font-size:14px;color:var(--navy);text-transform:uppercase}
.card-text{font-size:13.5px;line-height:26px;margin-top:8px;color:#333}
.card-link{margin-top:4px;font-size:14px;color:var(--blue);gap:10px}
.card.is-active{border-bottom:5px solid var(--blue)}

/* about */
.about{left:0;top:1769px;width:1200px;height:636px;background:linear-gradient(135deg,var(--blue) 0,var(--blue-2) 60%,#0a84c2 100%)}
.about-frame{left:112px;top:1929px;width:380px;height:372px;border:1px solid rgba(255,255,255,.8)}
.about-photo-main{left:124px;top:1872px;width:391px;height:422px;background:linear-gradient(140deg,#333c48 0,#dfe6ee 40%,#9bb8d6 75%,#eef3f7 100%)}
.about-photo-person{left:322px;top:2114px;width:220px;height:197px;background:linear-gradient(180deg,#f4f7fa 0,#c8d6e6 60%,#6f8cad 100%)}
.dots{background-image:radial-gradient(rgba(255,255,255,.85) 1px,transparent 1.5px);background-size:6px 6px}
.about-title{left:617px;top:1868px;font-size:35px;color:var(--white)}
.about-bar{left:617px;top:1912px;width:78px;height:4px;background:var(--white)}
.about-copy{left:617px;top:1944px;width:460px;font-size:15px;line-height:25.7px;color:var(--white);text-align:justify}
.about-btn{left:617px;top:2234px;width:173px;height:57px;padding-left:20px;color:var(--white);border:2px solid var(--white);border-left:none;border-top:none;background:var(--blue)}

/* projects */
.tile{border:3px solid var(--white);box-shadow:0 1px 6px rgba(0,0,0,.15)}

/* footer */
.footer-brand{left:107px;top:3330px;color:var(--white)}
.footer-about{left:107px;top:3402px;width:260px;font-size:15px;line-height:26px;color:#e8e8e8}
.footer-head{font-weight:700;font-size:15px;color:var(--white);text-transform:uppercase}
.footer-head::after{content:"";display:block;width:40px;height:2px;background:var(--blue);margin-top:12px}
.contact-item{display:flex;gap:20px;font-size:15px;line-height:23px;color:#eee}
.contact-item svg{flex:none;margin-top:4px}
.subscribe{left:771px;top:3421px;width:319px;height:43px;display:flex}
.subscribe-field{flex:1;background:#1c3a55;color:#dfe7ee;font-size:13px;display:flex;align-items:center;gap:14px;padding-left:14px}
.subscribe-btn{width:106px;background:var(--blue);color:var(--white);font-weight:700;font-size:14px;display:flex;align-items:center;justify-content:center}
.social{width:36px;height:36px;border-radius:50%}
.footer-rule{left:107px;top:3576px;width:986px;height:1px;background:#444}
.copyright{left:0;top:3596px;width:1200px;text-align:center;font-size:12px;color:#ddd}
</style>
</head>
<body>

<!-- header -->
<div class="abs topline"></div>
<header class="abs header">
  <div class="brand"><span class="brand-square"></span><span class="brand-name">MERIDIAN PM</span></div>
  <nav class="nav">
    <a class="active">HOME</a><a>ABOUT</a><a>SERVICES</a><a>BLOG</a><a>CONTACT US</a>
  </nav>
  <div class="phone">
    <span class="phone-icon"><svg width="16" height="16" viewBox="0 0 24 24"><path fill="#fff" d="M6.6 10.8a15 15 0 0 0 6.6 6.6l2.2-2.2a1 1 0 0 1 1-.25 11.4 11.4 0 0 0 3.6.57 1 1 0 0 1 1 1V20a1 1 0 0 1-1 1A17 17 0 0 1 3 4a1 1 0 0 1 1-1h3.5a1 1 0 0 1 1 1c0 1.25.2 2.45.57 3.57a1 1 0 0 1-.25 1z"/></svg></span>
    +1 555 010 0199
  </div>
  <div class="login">LOGIN <svg width="11" height="13" viewBox="0 0 11 13"><rect x="0" y="5" width="11" height="8" fill="#fff"/><path d="M2.5 5V3.5a3 3 0 0 1 6 0V5" stroke="#fff" stroke-width="1.8" fill="none"/></svg></div>
</header>

<!-- hero -->
<svg class="abs" style="left:0;top:85px" width="1200" height="792" viewBox="0 85 1200 792" role="img" aria-label="Photo of two colleagues reviewing documents at a laptop in a bright office">
  <defs>
    <linearGradient id="heroTone" x1="0" y1="0" x2="1" y2="0.4">
      <stop offset="0" stop-color="#aab6c2"/>
      <stop offset="0.35" stop-color="#5b6672"/>
      <stop offset="0.7" stop-color="#2f4252"/>
      <stop offset="1" stop-color="#1c3246"/>
    </linearGradient>
  </defs>
  <polygon points="0,85 1200,85 1200,741 1031,875 600,720 169,875 0,741" fill="url(#heroTone)"/>
  <polyline points="169,875 600,720 1031,875" fill="none" stroke="#0094D4" stroke-width="7"/>
</svg>
<div class="abs hero-text">
  <div class="hero-kicker display">Project Management</div>
  <div class="hero-title display">Meridian</div>
  <p class="hero-lead">Lorem ipsum dolor sit amet, consectetur adipiscing elit, sed do eiusmod tempor incididunt ut labore et</p>
  <div class="btn hero-btn">Get Started
    <svg width="16" height="16" viewBox="0 0 16 16"><circle cx="8" cy="8" r="8" fill="#fff"/><path d="M6.5 4.5 10 8l-3.5 3.5" stroke="#0a2a4a" stroke-width="2" fill="none"/></svg>
  </div>
</div>
<div class="abs slides"><div>01</div><div class="on">02</div><div>03</div></div>

<!-- certifications -->
<h2 class="abs section-title display" style="top:898px">My Certifications</h2>
<div class="abs title-bar" style="top:950px"></div>
<div class="abs cert" style="left:175px;top:1003px">
  <svg width="150" height="127" viewBox="0 0 150 127"><polygon points="10,90 40,75 40,110" fill="#F5BC92"/><polygon points="140,90 110,75 110,110" fill="#F5BC92"/><circle cx="75" cy="63" r="62" fill="#F5BC92"/><circle cx="75" cy="63" r="52" fill="#F08F49"/><circle cx="75" cy="63" r="38" fill="#EE7325"/></svg>
  Project Leadership Guild
</div>
<div class="abs cert" style="left:461px;top:1003px">
  <svg width="150" height="127" viewBox="0 0 150 127"><polygon points="10,90 40,75 40,110" fill="#F5BC92"/><polygon points="140,90 110,75 110,110" fill="#F5BC92"/><circle cx="75" cy="63" r="62" fill="#F5BC92"/><circle cx="75" cy="63" r="52" fill="#EE7325"/><circle cx="75" cy="63" r="38" fill="#F08F49"/></svg>
  Agile Practice Council
</div>
<div class="abs cert" style="left:749px;top:1003px">
  <svg width="150" height="127" viewBox="0 0 150 127"><polygon points="10,90 40,75 40,110" fill="#F5BC92"/><polygon points="140,90 110,75 110,110" fill="#F5BC92"/><circle cx="75" cy="63" r="62" fill="#F5BC92"/><circle cx="75" cy="63" r="52" fill="#F08F49"/><circle cx="75" cy="63" r="38" fill="#EE7325"/></svg>
  Scaled Team Lead
</div>

<!-- services -->
<h2 class="abs section-title display" style="top:1242px">Our Services</h2>
<div class="abs title-bar" style="top:1293px"></div>
<div class="abs dots" style="left:88px;top:1560px;width:160px;height:150px;opacity:.25;filter:invert(1)"></div>

<article class="abs card" style="left:112px;top:1348px">
  <div class="card-photo" role="img" aria-label="Photo of a professional working at a desk"></div>
  <div class="card-body">
    <div class="card-title">Lorem ipsum dolor sit</div>
    <p class="card-text">Lorem ipsum dolor consectetur adipiscing elite sed do eiusmod tempor incididunt ut labore eted</p>
    <div class="btn card-link">Read More <svg width="12" height="12" viewBox="0 0 16 16"><circle cx="8" cy="8" r="8" fill="#0094D4"/><path d="M6.5 4.5 10 8l-3.5 3.5" stroke="#fff" stroke-width="2" fill="none"/></svg></div>
  </div>
</article>
<article class="abs card" style="left:359px;top:1348px">
  <div class="card-photo" role="img" aria-label="Photo of a professional working at a desk"></div>
  <div class="card-body">
    <div class="card-title">Lorem ipsum dolor sit</div>
    <p class="card-text">Lorem ipsum dolor consectetur adipiscing elite sed do eiusmod tempor incididunt ut labore eted</p>
    <div class="btn card-link">Read More <svg width="12" height="12" viewBox="0 0 16 16"><circle cx="8" cy="8" r="8" fill="#0094D4"/><path d="M6.5 4.5 10 8l-3.5 3.5" stroke="#fff" stroke-width="2" fill="none"/></svg></div>
  </div>
</article>
<article class="abs card is-active" style="left:606px;top:1348px">
  <div class="card-photo" role="img" aria-label="Photo of a professional working at a desk"></div>
  <div class="card-body">
    <div class="card-title">Lorem ipsum dolor sit</div>
    <p class="card-text">Lorem ipsum dolor consectetur adipiscing elite sed do eiusmod tempor incididunt ut labore eted</p>
    <div class="btn card-link">Read More <svg width="12" height="12" viewBox="0 0 16 16"><circle cx="8" cy="8" r="8" fill="#0094D4"/><path d="M6.5 4.5 10 8l-3.5 3.5" stroke="#fff" stroke-width="2" fill="none"/></svg></div>
  </div>
</article>
<article class="abs card" style="left:854px;top:1348px">
  <div class="card-photo" role="img" aria-label="Photo of a professional working at a desk"></div>
  <div class="card-body">
    <div class="card-title">Lorem ipsum dolor sit</div>
    <p class="card-text">Lorem ipsum dolor consectetur adipiscing elite sed do eiusmod tempor incididunt ut labore eted</p>
    <div class="btn card-link">Read More <svg width="12" height="12" viewBox="0 0 16 16"><circle cx="8" cy="8" r="8" fill="#0094D4"/><path d="M6.5 4.5 10 8l-3.5 3.5" stroke="#fff" stroke-width="2" fill="none"/></svg></div>
  </div>
</article>

<!-- about -->
<section class="abs about"></section>
<div class="abs about-frame"></div>
<div class="abs dots" style="left:517px;top:1955px;width:28px;height:145px"></div>
<div class="abs dots" style="left:145px;top:2296px;width:150px;height:28px"></div>
<div class="abs about-photo-main" role="img" aria-label="Photo of hands reviewing charts on a clipboard beside a laptop"></div>
<div class="abs about-photo-person" role="img" aria-label="Portrait of the consultant in a blue suit"></div>
<h2 class="abs about-title display">About Me</h2>
<div class="abs about-bar"></div>
<p class="abs about-copy">Marcus Ellery is the Owner of Project Management Meridian, LLC and serves as Principal Lead Consultant on waterfall and agile contract opportunities. Project Management Meridian, LLC has engaged on a contract basis with Vantage 400 companies across various industries including banking and credit unions, global supply chain, and international food distribution. Marcus Ellery brings 12 years of experience to his clients encompassing various project methodologies including: waterfall, agile, and hybrid frameworks. Most recently, Project Management Meridian, LLC has took on PM consulting contracts in the agile transformation space.</p>
<div class="abs btn about-btn">Learn More
  <svg width="16" height="16" viewBox="0 0 16 16"><circle cx="8" cy="8" r="8" fill="#fff"/><path d="M6.5 4.5 10 8l-3.5 3.5" stroke="#0094D4" stroke-width="2" fill="none"/></svg>
</div>

<!-- past projects -->
<h2 class="abs section-title display" style="top:2484px">Past Projects</h2>
<div class="abs title-bar" style="top:2534px"></div>
<div class="abs tile" style="left:114px;top:2588px;width:233px;height:215px;background:linear-gradient(135deg,#e9eef2,#b9c6d1 60%,#7c8a96)" role="img" aria-label="Photo of a laptop and tablet showing charts"></div>
<div class="abs tile" style="left:360px;top:2588px;width:233px;height:215px;background:linear-gradient(135deg,#cfd8e0,#8a6a5e 55%,#e8ecef)" role="img" aria-label="Photo of a developer holding a laptop in front of monitors"></div>
<div class="abs tile" style="left:606px;top:2588px;width:233px;height:215px;background:linear-gradient(135deg,#f1f3f5,#c7d3df 55%,#6e7f8f)" role="img" aria-label="Photo of hands working with documents and a laptop"></div>
<div class="abs tile" style="left:853px;top:2588px;width:233px;height:215px;background:linear-gradient(135deg,#1d3550,#3f6a90 55%,#0f1f30)" role="img" aria-label="Photo of an engineer with a tablet in a server room"></div>
<div class="abs tile" style="left:116px;top:2818px;width:431px;height:214px;background:linear-gradient(135deg,#3a3a40,#8e8a86 50%,#d9d6d0)" role="img" aria-label="Photo of a team meeting around a whiteboard"></div>
<div class="abs tile" style="left:561px;top:2818px;width:257px;height:214px;background:linear-gradient(135deg,#2f77b5,#5d9ed6 60%,#2a5d8f)" role="img" aria-label="Photo of two colleagues working at a laptop, blue tinted"></div>
<div class="abs tile" style="left:829px;top:2818px;width:257px;height:214px;background:linear-gradient(135deg,#1f4f7a,#e59a4a 55%,#17324e)" role="img" aria-label="Photo of hands typing on a glowing keyboard"></div>

<!-- footer -->
<svg class="abs" style="left:0;top:3100px" width="1200" height="537" viewBox="0 3100 1200 537">
  <polygon points="0,3233 169,3106 600,3262 1031,3106 1200,3233 1200,3637 0,3637" fill="#050505"/>
  <polyline points="169,3106 600,3262 1031,3106" fill="none" stroke="#0094D4" stroke-width="7"/>
</svg>
<div class="abs brand footer-brand"><span class="brand-square"></span><span class="brand-name">MERIDIAN PM</span></div>
<p class="abs footer-about">Lorem ipsum dolor sit consectetur adipiscing sed do eiusmod tempor incididunted uteixd laboregd eted.</p>

<div class="abs footer-head" style="left:474px;top:3325px">Contact Information</div>
<div class="abs contact-item" style="left:474px;top:3374px">
  <svg width="18" height="18" viewBox="0 0 24 24"><path fill="#fff" d="M22 2 2 11l8 3 3 8z"/></svg>
  <span>345,Lorem ipsum dolor sit<br>consectetur adipiscinget.</span>
</div>
<div class="abs contact-item" style="left:474px;top:3441px">
  <svg width="18" height="14" viewBox="0 0 18 14"><rect width="18" height="14" fill="#fff"/><path d="M0 0 9 7 18 0" stroke="#050505" stroke-width="1.5" fill="none"/></svg>
  <span>Email:info@meridianpm.example</span>
</div>
<div class="abs contact-item" style="left:474px;top:3485px">
  <svg width="16" height="16" viewBox="0 0 24 24"><path fill="#fff" d="M6.6 10.8a15 15 0 0 0 6.6 6.6l2.2-2.2a1 1 0 0 1 1-.25 11.4 11.4 0 0 0 3.6.57 1 1 0 0 1 1 1V20a1 1 0 0 1-1 1A17 17 0 0 1 3 4a1 1 0 0 1 1-1h3.5a1 1 0 0 1 1 1c0 1.25.2 2.45.57 3.57a1 1 0 0 1-.25 1z"/></svg>
  <span>Phone: +1 555 010 0199</span>
</div>

<div class="abs footer-head" style="left:771px;top:3325px">Newsletter</div>
<p class="abs" style="left:771px;top:3379px;font-size:15px;color:#eee">Enter your email &amp; subcribing newsletter</p>
<div class="abs subscribe">
  <div class="subscribe-field">
    <svg width="14" height="11" viewBox="0 0 18 14"><rect width="18" height="14" fill="#0094D4"/><path d="M0 0 9 7 18 0" stroke="#1c3a55" stroke-width="1.5" fill="none"/></svg>
    Email address
  </div>
  <div class="subscribe-btn">SUBSCRIBE</div>
</div>
<div class="abs social" style="left:773px;top:3492px;background:#1f4d8f" aria-label="Social link"></div>
<div class="abs social" style="left:815px;top:3492px;background:#1da1e2" aria-label="Social link"></div>
<div class="abs social" style="left:858px;top:3492px;background:#d9473a" aria-label="Social link"></div>
<div class="abs social" style="left:901px;top:3492px;background:#c8202a" aria-label="Social link"></div>

<div class="abs footer-rule"></div>
<p class="abs copyright">2022 © Copyrights Meridian All rights reserved.</p>

</body>
</html>
```